Brightlane Rapid Rinse Web Design

We are looking for a web design that highlights our state of the art fully automated commercial vehicle washing equipment. Similar system to a car wash however this system is meant for the largest vehicles on our roadways. Transport trucks with or without a trailer, busses both highway and school, RV's from 5th wheel type to A Class. Cement trucks, dump trucks, vac trucks, fuel trucks etc. Pick ups with utility trailers...Refrigerator truck clean outs.
Brightlane Rapid Rinse will wash your vehicle quickly and with a minimal impact on the environment

Home page
About us
Why Brightlane
Services and pricing
Videos of wash system
Fleets
contact us

Target Market(s)

Commercial vehicle owners and operators as well as corporate fleets. Includes busses, municipal, school and highway.both school and

Industry/Entity Type

transportation

Coding

Coded - Design and coding required

Number of Pages Required

5+ page

Font styles to use
Sans Serif

Colors
0054AA
0677BA
7BADD7
CADEEF
E8F1F8

Requirements
Must have
• Welcome page,why us page which describes the financial and environmental benefits. payment processing page, contact us page, Services which is washing vehicles and greasing for commercial vehicles that want that service and grease
Nice to have
• pictures of both clean and dirty commercial vehicles ie. before and after

```html
<!DOCTYPE html>
<html lang="en">
<head>
<meta charset="utf-8">
<title>Brightlane Rapid Rinse</title>
<link href="https://fonts.googleapis.com/css2?family=Rubik:wght@500;700;800&family=Roboto:wght@400;500;700&display=swap" rel="stylesheet">
<style>
:root{
  --blue:#0054AA;
  --blue-mid:#0677BA;
  --blue-soft:#7BADD7;
  --blue-pale:#CADEEF;
  --blue-mist:#E8F1F8;
  --ink:#1b1b1b;
  --grey:#6b6b6b;
  --white:#fff;
}
*{margin:0;padding:0;box-sizing:border-box}
html,body{width:1200px;height:5072px;overflow:hidden}
body{font-family:'Roboto',sans-serif;color:var(--ink);background:var(--white);position:relative}
.abs{position:absolute}
h1,h2,h3{font-family:'Rubik',sans-serif;font-weight:800;letter-spacing:.5px}
.section-title{color:var(--blue);font-size:44px;text-align:center}
.lead{color:var(--grey);font-size:13.5px;line-height:30px;text-align:center;width:780px;margin:0 auto}
.body-text{color:var(--grey);font-size:13.5px;line-height:31px}
.btn{display:inline-flex;align-items:center;justify-content:center;height:38px;padding:0 26px;border-radius:19px;font-size:13px;font-weight:700;text-decoration:none}
.btn-blue{background:var(--blue);color:var(--white);box-shadow:0 4px 10px rgba(0,84,170,.3)}
.btn-white{background:var(--white);color:var(--blue)}
.photo{position:absolute}

/* hero */
.hero{position:absolute;left:0;top:0;width:1200px;height:640px;background:linear-gradient(160deg,#5c6670 0%,#3c4650 45%,#8f9aa3 70%,#2d3338 100%)}
.brand-block{position:absolute;left:0;top:0;width:360px;height:102px;background:rgba(20,24,28,.55)}
.brand-name{position:absolute;left:112px;top:26px;color:var(--white);font-family:'Rubik',sans-serif;font-weight:700;font-size:24px;line-height:38px;text-transform:uppercase}
.topbar{position:absolute;left:345px;top:0;width:855px;height:53px;background:var(--white);clip-path:polygon(0 0,100% 0,100% 100%,20px 100%)}
.contact{position:absolute;top:17px;display:flex;align-items:center;gap:12px;font-size:14px;color:#333}
.contact svg{width:16px;height:16px}
.get-touch{position:absolute;left:960px;top:9px;height:34px;font-size:12px;padding:0 26px}
.navbar{position:absolute;left:338px;top:53px;width:862px;height:50px;background:var(--blue);clip-path:polygon(20px 0,100% 0,100% 100%,0 100%)}
.navbar ul{list-style:none;display:flex;position:absolute;left:74px;top:16px;gap:0}
.navbar li{color:var(--white);font-size:14px;margin-right:48px}
.play{position:absolute;left:564px;top:208px;width:72px;height:72px;border-radius:50%;background:rgba(255,255,255,.35);display:flex;align-items:center;justify-content:center}
.play span{width:50px;height:50px;border-radius:50%;background:var(--white);display:flex;align-items:center;justify-content:center}
.hero-title{position:absolute;left:0;top:305px;width:1200px;text-align:center;color:var(--white);font-size:70px;line-height:84px;text-shadow:0 3px 8px rgba(0,0,0,.35)}
.hero-btns{position:absolute;top:493px;left:0;width:1200px;display:flex;justify-content:center;gap:22px}

/* about */
.about-bar{left:167px;top:780px;width:20px;height:170px;background:var(--blue);border-radius:10px}
.about-arc{left:420px;top:1010px;width:152px;height:180px;background:var(--blue-mid);border-radius:0 0 150px 0}
.about-heading{left:683px;top:805px;color:var(--blue);font-size:44px}
.about-text{left:683px;top:878px;width:400px}

/* offer */
.card-photo{top:1569px;width:313px;height:252px}
.card-panel{top:1766px;width:276px;height:272px;color:var(--white);text-align:center;padding:36px 18px 0}
.card-panel h3{font-size:15px;font-weight:700;letter-spacing:.3px;margin-bottom:14px}
.card-panel p{font-size:12px;line-height:26.5px;margin-bottom:12px}
.card-panel .btn{height:34px;font-size:11.5px;padding:0 30px}

/* mission */
.mission-photo{left:0;top:2180px;width:1200px;height:486px;background:linear-gradient(100deg,#4d5a52 0%,#7b8c80 50%,#3a3f36 100%)}
.mission-shape{left:0;top:2180px;width:660px;height:486px;background:var(--blue);border-radius:0 330px 330px 0/0 260px 260px 0}
.mission-heading{left:112px;top:2234px;color:var(--white);font-size:44px}
.mission-text{left:112px;top:2298px;width:400px;color:var(--white)}

/* portfolio */
.slider{left:134px;top:2916px;width:932px;height:476px;background:var(--white);border-radius:16px;box-shadow:0 4px 20px rgba(0,0,0,.12)}
.slide-before{left:142px;top:2924px;width:458px;height:460px;background:linear-gradient(135deg,#8b9095,#5c6166 55%,#3a3e42);border-radius:12px 0 0 12px}
.slide-after{left:600px;top:2924px;width:458px;height:460px;background:linear-gradient(180deg,#dbe6f1 0%,#f3f5f7 45%,#a9b3bb 100%);border-radius:0 12px 12px 0}
.slide-handle{left:578px;top:3133px;width:44px;height:44px;border-radius:50%;background:var(--white);display:flex;align-items:center;justify-content:center}
.slide-arrow{width:22px;height:22px;border-radius:50%;border:2px solid var(--grey);display:flex;align-items:center;justify-content:center}

/* why */
.why-photo{left:110px;top:3548px;width:479px;height:510px;border-radius:14px;background:linear-gradient(135deg,#3b4048,#8d949b 55%,#d9dde0)}
.why-heading{left:648px;top:3574px;color:var(--blue);font-size:44px}
.why-text{left:648px;top:3642px;width:440px}

/* contact */
.contact-band{left:0;top:4194px;width:1200px;height:571px;background:var(--blue)}
.contact-heading{left:0;top:4276px;width:1200px;text-align:center;color:var(--white);font-size:44px}
.contact-lead{left:0;top:4350px;width:1200px;text-align:center;color:var(--white);font-size:13.5px}
.field{left:220px;width:362px;height:50px;border-radius:25px;background:var(--white);color:var(--grey);font-size:12px;padding:18px 30px}
.message{left:618px;top:4418px;width:362px;height:250px;border-radius:20px;background:var(--white);color:var(--grey);font-size:12px;padding:18px 20px}
.send{left:220px;top:4627px;width:362px;height:48px;border-radius:24px;background:linear-gradient(180deg,var(--blue-mid),var(--blue));color:var(--white);font-size:13px;font-weight:700;display:flex;align-items:center;justify-content:center;box-shadow:0 4px 10px rgba(0,0,0,.25)}

/* footer */
.footer-name{left:0;top:4836px;width:1200px;text-align:center;color:var(--blue);font-size:32px}
.footer-nav{left:0;top:4906px;width:1200px;display:flex;justify-content:center;gap:46px;font-size:14px;color:#444;list-style:none}
.socials{left:0;top:4952px;width:1200px;display:flex;justify-content:center;gap:14px}
.socials span{width:40px;height:40px;border-radius:50%;background:var(--blue);display:flex;align-items:center;justify-content:center}
.socials span i{width:14px;height:14px;border-radius:50%;background:var(--blue-pale)}
.legal{left:0;top:5016px;width:1200px;display:flex;justify-content:center;gap:60px;font-size:12px;color:#555}
.legal a{color:var(--blue);text-decoration:none}
</style>
</head>
<body>

<header class="hero" role="img" aria-label="Photo of a commercial truck being pressure washed with spray">
</header>
<div class="brand-block"></div>
<div class="brand-name">Brightlane<br>Rapid Rinse</div>
<div class="topbar">
  <div class="contact" style="left:64px">
    <svg viewBox="0 0 16 16"><rect width="16" height="16" rx="3" fill="#0054AA"/><path d="M5 4l2 .3.6 2-1.1.8a6 6 0 002.4 2.4l.8-1.1 2 .6.3 2c-4.3.4-7.4-2.7-7-7z" fill="#fff"/></svg>
    +1 555 010 2024
  </div>
  <div class="contact" style="left:268px">
    <svg viewBox="0 0 16 16"><rect y="3" width="16" height="11" rx="1.5" fill="#0054AA"/><path d="M1 4l7 5 7-5" stroke="#fff" stroke-width="1.4" fill="none"/></svg>
    info@brightlanerapidrinse.com
  </div>
  <a class="btn btn-blue get-touch" style="left:615px">Get In Touch</a>
</div>
<nav class="navbar">
  <ul>
    <li>Home</li><li>About Us</li><li>Why Brightlane</li><li>Services &amp; Pricing</li><li>Videos</li><li>Fleets</li>
  </ul>
</nav>
<div class="play"><span><svg width="16" height="18" viewBox="0 0 16 18"><path d="M2 1l13 8-13 8z" fill="#1b1b1b"/></svg></span></div>
<h1 class="hero-title">BRIGHTLANE RAPID<br>RINSE</h1>
<div class="hero-btns">
  <a class="btn btn-blue" style="width:124px">Book A Wash</a>
  <a class="btn btn-white" style="width:124px">Learn More</a>
</div>

<!-- About -->
<div class="abs about-bar"></div>
<div class="abs about-arc"></div>
<div class="photo" role="img" aria-label="Photo of a yellow cement mixer truck" style="left:207px;top:780px;width:392px;height:323px;border-radius:16px;background:linear-gradient(135deg,#7e8a92,#d8b531 55%,#5b5f60)"></div>
<div class="photo" role="img" aria-label="Photo of a truck wheel being pressure washed" style="left:122px;top:970px;width:390px;height:324px;border-radius:16px;background:linear-gradient(135deg,#2c3036,#8e959b 50%,#3a3d42);box-shadow:0 10px 24px rgba(0,0,0,.25)"></div>
<h2 class="abs about-heading">ABOUT US</h2>
<div class="abs about-text body-text">
  <p>At vero eos et accusamus et iusto odio dignissimos ducimus qui blanditiis praesentium voluptatum deleniti atque corrupti quos dolores et quas molestias excepturi sint occaecati cupiditate non provident, similique sunt in culpa qui officia deserunt mollitia animi, id est laborum et dolorum fuga.</p>
  <p style="margin-top:31px">Nam libero tempore, cum soluta nobis est eligendi optio cumque nihil impedit quo minus id quod maxime placeat facere possimus, omnis voluptas assumenda est, omnis dolor repellendus.</p>
  <a class="btn btn-blue" style="margin-top:30px;height:34px;font-size:12px">Read More</a>
</div>

<!-- What we offer -->
<h2 class="abs section-title" style="left:0;top:1400px;width:1200px">WHAT WE OFFER</h2>
<p class="abs lead" style="left:210px;top:1472px">Sed ut perspiciatis unde omnis iste natus error sit voluptatem accusantium doloremque laudantium, totam rem aperiam, eaque ipsa quae ab illo inventore veritatis et quasi architecto beatae vitae dicta sunt explicabo. Nemo enim ipsam volupt</p>

<div class="photo card-photo" role="img" aria-label="Photo of a worker in an automated truck wash bay" style="left:104px;background:linear-gradient(135deg,#6c6f74,#c9cbcf 50%,#7d8087)"></div>
<div class="abs card-panel" style="left:124px;background:var(--blue);clip-path:polygon(0 0,100% 0,100% 90%,0 100%)">
  <h3>AUTOMATED TRUCK WASH</h3>
  <p>Sed ut perspiciatis unde omnis iste natus error sit voluptatem accusantium doloremque laudantium, totam rem aperiam, eaque ipsa</p>
  <a class="btn btn-white">Read More</a>
</div>

<div class="photo card-photo" role="img" aria-label="Photo of a truck front being pressure washed" style="left:443px;background:linear-gradient(135deg,#3a3d42,#a33a3a 40%,#9aa0a6)"></div>
<div class="abs card-panel" style="left:461px;background:var(--blue-mid);clip-path:polygon(0 0,100% 0,100% 100%,0 92%)">
  <h3>ADDITIONAL SERVICES</h3>
  <p>Sed ut perspiciatis unde omnis iste natus error sit voluptatem accusantium doloremque laudantium, totam rem aperiam, eaque ipsa</p>
  <a class="btn btn-white">Read More</a>
</div>

<div class="photo card-photo" role="img" aria-label="Illustration of connected fleet trucks on a highway at sunset" style="left:782px;background:linear-gradient(160deg,#6d8aa8,#c7d6e3 45%,#e0a878 70%,#5b6f84)"></div>
<div class="abs card-panel" style="left:800px;background:var(--blue);clip-path:polygon(0 0,100% 0,100% 90%,0 100%)">
  <h3>FLEET SERVICES</h3>
  <p>Sed ut perspiciatis unde omnis iste natus error sit voluptatem accusantium doloremque laudantium, totam rem aperiam, eaque ipsa</p>
  <a class="btn btn-white">Read More</a>
</div>

<!-- Mission -->
<div class="photo mission-photo" role="img" aria-label="Photo of a man pressure washing a truck outdoors"></div>
<div class="abs mission-shape"></div>
<h2 class="abs mission-heading">OUR MISSION</h2>
<div class="abs mission-text body-text" style="color:var(--white)">
  <p>At vero eos et accusamus et iusto odio dignissimos ducimus qui blanditiis praesentium voluptatum deleniti atque corrupti quos dolores et quas molestias excepturi sint occaecati cupiditate non provident, similique sunt in culpa qui officia deserunt mollitia animi, id est laborum et dolorum fuga.</p>
  <p style="margin-top:31px">Nam libero tempore, cum soluta nobis est eligendi optio cumque nihil impedit quo minus id quod maxime</p>
  <a class="btn btn-blue" style="margin-top:30px;height:34px;font-size:12px;box-shadow:0 4px 10px rgba(0,0,0,.3)">Read More</a>
</div>

<!-- Portfolio -->
<h2 class="abs section-title" style="left:0;top:2754px;width:1200px">OUR PORTFOLIO</h2>
<p class="abs lead" style="left:210px;top:2828px">Sed ut perspiciatis unde omnis iste natus error sit voluptatem accusantium doloremque laudantium, totam rem aperiam, eaque ipsa quae ab illo inventore veritatis et quasi architecto beatae vitae dicta sunt explicabo. Nemo enim ipsam volupt</p>
<div class="abs slider"></div>
<div class="photo slide-before" role="img" aria-label="Before: dirty commercial truck in a wash bay"></div>
<div class="photo slide-after" role="img" aria-label="After: clean white semi truck on the road"></div>
<div class="abs slide-handle"><svg width="18" height="10" viewBox="0 0 18 10"><path d="M0 5l6-5v10zM18 5l-6-5v10z" fill="#0054AA"/></svg></div>
<div class="abs slide-arrow" style="left:1084px;top:3128px"><svg width="10" height="10" viewBox="0 0 10 10"><path d="M1 5h8M5 1l4 4-4 4" stroke="#6b6b6b" stroke-width="1.6" fill="none"/></svg></div>
<div class="abs slide-arrow" style="left:1084px;top:3158px;border-color:#c4c4c4"><svg width="10" height="10" viewBox="0 0 10 10"><path d="M9 5H1M5 1L1 5l4 4" stroke="#c4c4c4" stroke-width="1.6" fill="none"/></svg></div>
<a class="abs btn btn-blue" style="left:543px;top:3424px;height:36px;font-size:12px;padding:0 24px">View More</a>

<!-- Why -->
<div class="photo why-photo" role="img" aria-label="Photo of a worker washing a truck wheel with a spray wand"></div>
<h2 class="abs why-heading">WHY BRIGHTLANE</h2>
<div class="abs why-text body-text">
  <p>At vero eos et accusamus et iusto odio dignissimos ducimus qui blanditiis praesentium voluptatum deleniti atque corrupti quos dolores et quas molestias excepturi sint occaecati cupiditate non provident, similique sunt in culpa qui officia deserunt mollitia animi, id est laborum et dolorum fuga.</p>
  <p style="margin-top:31px">Nam libero tempore, cum soluta nobis est eligendi optio cumque nihil impedit quo minus id quod maxime placeat facere possimus, omnis voluptas assumenda est, omnis dolor repellendus. Temporibus autem quibusdam et aut officiis debitis</p>
  <a class="btn btn-blue" style="margin-top:30px;height:34px;font-size:12px">Read More</a>
</div>

<!-- Contact -->
<section class="abs contact-band"></section>
<h2 class="abs contact-heading">GET IN TOUCH WITH US</h2>
<p class="abs contact-lead">Sed ut perspiciatis unde omnis iste natus error sit voluptatem accusantium doloremque laudantium, totam</p>
<div class="abs field" style="top:4418px">Full Name</div>
<div class="abs field" style="top:4487px">Email Address</div>
<div class="abs field" style="top:4557px">Contact Number</div>
<div class="abs message">Message</div>
<div class="abs send">Send Message</div>

<!-- Footer -->
<h2 class="abs footer-name">BRIGHTLANE RAPID RINSE</h2>
<ul class="abs footer-nav">
  <li>Home</li><li>About Us</li><li>Why Brightlane</li><li>Services &amp; Pricing</li><li>Videos</li><li>Fleets</li>
</ul>
<div class="abs socials">
  <span><i></i></span><span><i></i></span><span><i></i></span><span><i></i></span><span><i></i></span>
</div>
<div class="abs legal">
  <span>(C) Copyright 2024 | All Rights Reserved</span>
  <a>Privacy Policy</a>
</div>

</body>
</html>
```